UI Improvement for FlorKeep app

We are looking for a talented UI/UX designer to REFINE and enhance the visual design of our mobile application, FlorKeep. The app is fully functional, but we need a designer to improve its aesthetics by specifying design elements such as fonts, colors, spacing, and component styles.
Your task will be to analyze the CURRENT UI and provide detailed design specifications that will make the app more visually appealing, modern, and user-friendly.
TODO:
Review the existing FlorKeep app design (see attachments) and identify areas for visual improvement.
Provide a detailed UI style guide, including:
Typography (font choices, sizes, and weights)
Color palette (primary, secondary, and accent colors)
Component styling (buttons, forms, icons, and interactive elements)
Spacing and layout guidelines (margins, paddings, and alignment)
Ensure the design remains clean, modern, and professional while maintaining usability and accessibility.
Provide design mockups or visual examples (if possible) to illustrate the proposed changes.
Deliverables:
A UI Style Guide (PDF or Figma file) with specifications on fonts, colors, spacing, and UI components.
Optionally, before/after mockups or examples demonstrating the improvements.
Ideal Designer:
Strong experience in mobile UI/UX design.
Understanding of modern design trends and best practices.
Ability to communicate design choices clearly for easy developer implementation.
I have attached 7 images showcasing the main UI screens used in the FlorKeep app. These screens need visual enhancements to improve their overall look and user experience.
The images represent the current design in three key modes:
LIST Mode – Displays data in a structured list format.
READ Mode – Shows detailed information when a user selects an item.
ADD/EDIT Mode – Allows users to input or modify information.
Additionally, there is a ‘MORE’ page, which serves as a menu listing other features of the application.
Task Objective:
Please refine and improve these UIs to create a more modern, visually appealing, and user-friendly experience. Focus on typography, colors, spacing, and component styling to ensure a cohesive and polished design.
Look and feel
Each slider illustrates characteristics of the customer's brand and the style your logo design should communicate.

```html
<!DOCTYPE html>
<html lang="en">
<head>
<meta charset="utf-8">
<title>FlorKeep app – UI style guide</title>
<link href="https://fonts.googleapis.com/css2?family=Figtree:wght@400;500;600;700;800&family=Nunito+Sans:wght@400;600;700;800&family=Roboto:wght@400;500;700&display=swap" rel="stylesheet">
<style>
:root{
  --blue:#1B7ECC; --ink:#1C1F34; --slate:#4B4B5A; --grey:#636669; --muted:#7C848B;
  --bg:#F2F6F7; --line:#E2E7F1;
  --cyan:#25C2E3; --green:#29BA85; --orange:#F77E53; --yellow:#FFBE0B; --pink:#FF5C75; --violet:#7859F4;
  --old-bar:#EEF0F3; --frame:#111;
}
*{box-sizing:border-box;margin:0;padding:0}
html,body{width:1017px;height:1200px;overflow:hidden;background:#fff}
.sheet{position:absolute;left:0;top:0;width:1760px;height:2076px;transform:scale(.5778);transform-origin:0 0;font-family:"Figtree",sans-serif;color:#000}
.abs{position:absolute}
.title{left:106px;top:100px;font-size:74px;font-weight:700;letter-spacing:-1px}
.section-label{top:228px;font-size:24px;font-weight:600;color:var(--muted)}
.swatch{position:absolute;width:71px;height:71px;border-radius:4px;display:flex;align-items:center;justify-content:center;font-size:15px;color:#fff}
.swatch.light{color:var(--ink)}
.font-sample{left:706px;font-size:60px;color:var(--ink)}
.band{left:106px;top:637px;width:1552px;height:65px;background:#000;color:#fff;font-size:26px;font-weight:700;padding:17px 18px}

/* legacy screens */
.legacy{position:absolute;width:344px;height:743px;top:737px;background:#fff;font-family:"Roboto",sans-serif;overflow:hidden}
.statusbar{height:43px;background:#000;color:#fff;font-size:15px;font-weight:500;position:relative}
.statusbar .time{position:absolute;left:46px;top:13px}
.statusbar svg{position:absolute;right:30px;top:15px}
.legacy-head{height:52px;background:var(--old-bar);position:relative;font-size:14px;color:#222}
.legacy-head .sub{position:absolute;left:0;right:0;text-align:center}
.legacy-body{position:absolute;top:95px;left:0;right:0;height:581px;background:#d9d9dc}
.legacy-card{position:absolute;left:6px;right:6px;background:#fff}
.ofield{position:absolute;height:41px;border:1.4px solid var(--blue);border-radius:3px;font-size:13px;color:#777;padding:12px 14px;white-space:nowrap;overflow:hidden}
.ofield .leg{position:absolute;top:-8px;left:9px;background:#fff;padding:0 3px;font-size:10px;font-weight:500;color:var(--blue);line-height:14px}
.ofield{overflow:visible}
.hint{position:absolute;font-size:10px;color:#8fb4dd}
.kebab{position:absolute;font-size:16px;font-weight:700;color:#222;letter-spacing:1px}
.legacy-tabs{position:absolute;top:676px;left:0;right:0;height:42px;background:#fff;display:flex;justify-content:space-around;border-top:1px solid #eee}
.legacy-tabs div{width:69px;text-align:center;font-size:10px;color:#222;padding-top:4px}
.legacy-tabs .on{color:var(--blue)}
.legacy-tabs svg{display:block;margin:0 auto 4px}
.home-bar{position:absolute;height:4px;border-radius:2px;background:#555}
.menu-row{height:37px;border-bottom:1px solid #ddd;display:flex;align-items:center;font-size:10px;color:#111;padding-left:12px}
.menu-row svg{margin-right:16px}

/* refined screens */
.phone{position:absolute;top:727px;width:364px;border:11px solid var(--frame);border-radius:58px;overflow:hidden;background:var(--bg);font-family:"Nunito Sans",sans-serif}
.phone .hero{position:absolute;left:0;top:0;right:0;height:174px;background:var(--blue)}
.island{position:absolute;left:115px;top:9px;width:112px;height:32px;border-radius:16px;background:#000}
.phone .time{position:absolute;left:31px;top:15px;color:#fff;font-size:16px;font-weight:700;font-family:"Figtree",sans-serif}
.phone .status-icons{position:absolute;right:22px;top:19px}
.dots{position:absolute;right:12px;top:60px}
.page-title{position:absolute;left:13px;top:86px;color:#fff;font-size:30px;font-weight:800;font-family:"Figtree",sans-serif}
.card{position:absolute;left:13px;width:316px;background:#fff;border-radius:12px;padding:0 14px}
.card-head{height:48px;border-bottom:1px solid var(--line);display:flex;align-items:center;justify-content:space-between;font-size:15px;font-weight:800;color:var(--ink)}
.field-label{font-size:14px;color:var(--grey);margin-top:14px;height:18px}
.input{margin-top:6px;height:47px;background:var(--bg);border:1px solid var(--line);border-radius:6px;padding:13px 13px;font-size:15px;color:#b8bec4;display:flex;justify-content:space-between;align-items:flex-start}
.input.tall{height:85px}
.split{display:flex;gap:14px}.split>div{flex:1}
.btn-save{position:absolute;left:13px;top:1132px;width:316px;height:47px;border-radius:24px;background:var(--blue);color:#fff;font-weight:700;font-size:15px;display:flex;align-items:center;justify-content:center}
.phone .home-bar{background:#000;height:4px}
.tiles{position:absolute;left:13px;top:139px;display:grid;grid-template-columns:153px 153px;gap:8px}
.tile{height:70px;background:#fff;border-radius:10px;display:flex;align-items:center;padding-left:13px;font-size:15px;color:var(--ink);line-height:18px}
.tile .ico{width:36px;height:36px;border-radius:50%;display:flex;align-items:center;justify-content:center;margin-right:14px;flex:none}
.tabbar{position:absolute;left:0;right:0;top:662px;height:82px;background:#fff;display:flex;justify-content:space-around;padding:10px 4px 0}
.tabbar div{width:58px;text-align:center;font-size:10px;color:var(--muted);position:relative}
.tabbar svg{display:block;margin:0 auto 4px}
.tabbar .on{color:var(--blue);font-weight:700}
.tabbar .on::before{content:"";position:absolute;left:3px;right:3px;top:0;height:28px;border-radius:14px;background:#e3effa;z-index:0}
.tabbar .on svg{position:relative}
</style>
</head>
<body>
<div class="sheet">
  <div class="abs title">FlorKeep app</div>
  <div class="abs section-label" style="left:106px">Colors</div>
  <div class="abs section-label" style="left:706px">Fonts</div>

  <div class="swatch" style="left:106px;top:277px;background:var(--blue)">1B7ECC</div>
  <div class="swatch" style="left:191px;top:277px;background:var(--ink)">1C1F34</div>
  <div class="swatch" style="left:275px;top:277px;background:var(--slate)">4B4B5A</div>
  <div class="swatch" style="left:360px;top:277px;background:var(--grey)">636669</div>
  <div class="swatch" style="left:444px;top:277px;background:var(--muted)">7C848B</div>
  <div class="swatch light" style="left:106px;top:369px;background:var(--bg)">F2F6F7</div>
  <div class="swatch light" style="left:191px;top:369px;background:var(--line)">E2E7F1</div>
  <div class="swatch" style="left:106px;top:461px;background:var(--cyan)">25C2E3</div>
  <div class="swatch" style="left:191px;top:461px;background:var(--green)">29BA85</div>
  <div class="swatch" style="left:275px;top:461px;background:var(--orange)">F77E53</div>
  <div class="swatch" style="left:360px;top:461px;background:var(--yellow)">FFBE0B</div>
  <div class="swatch" style="left:444px;top:461px;background:var(--pink)">FF5C75</div>
  <div class="swatch" style="left:529px;top:461px;background:var(--violet)">7859F4</div>

  <div class="abs font-sample" style="top:272px;font-family:'Figtree',sans-serif">Figtree</div>
  <div class="abs font-sample" style="top:364px;font-family:'Nunito Sans',sans-serif">Nunito Sans</div>

  <div class="abs band">Add-Edit Page &amp; More page</div>

  <!-- legacy add contact -->
  <div class="legacy" style="left:106px">
    <div class="statusbar"><span class="time">10:37</span>
      <svg width="70" height="14"><g fill="#777"><circle cx="3" cy="11" r="1.2"/><circle cx="7" cy="11" r="1.2"/><circle cx="11" cy="11" r="1.2"/><circle cx="15" cy="11" r="1.2"/></g><path d="M24 5a10 10 0 0 1 14 0M27 8a6 6 0 0 1 8 0" stroke="#fff" stroke-width="2" fill="none"/><circle cx="31" cy="11" r="1.6" fill="#fff"/><rect x="45" y="2" width="21" height="10" rx="3" fill="#fff"/></svg>
    </div>
    <div class="legacy-head">
      <svg class="abs" style="left:16px;top:19px" width="16" height="14"><path d="M15 7H2M7 1L1 7l6 6" stroke="#222" stroke-width="2" fill="none"/></svg>
      <div class="sub" style="top:11px;font-size:10px;color:#666">Add</div>
      <div class="sub" style="top:23px">Contact</div>
      <div class="abs" style="left:273px;top:18px;color:var(--blue);font-size:13px;font-weight:500">Save</div>
      <div class="kebab" style="left:312px;top:12px">•••</div>
    </div>
    <div class="legacy-body">
      <div class="legacy-card" style="top:6px;height:294px">
        <div class="ofield" style="left:8px;top:18px;width:285px"><span class="leg">Business Name -e</span>enter contactbusinessname -e</div>
        <div class="kebab" style="left:309px;top:32px;font-size:12px">•••</div>
        <div class="ofield" style="left:8px;top:82px;width:315px"><span class="leg">First Name -e</span>enter contactfirstname -e</div>
        <div class="ofield" style="left:8px;top:146px;width:315px"><span class="leg">Middle Name -e</span>enter contactmiddlename -e</div>
        <div class="ofield" style="left:8px;top:210px;width:315px"><span class="leg">Last Name -e</span>enter contactlastname -e</div>
        <div class="abs" style="left:6px;right:6px;top:282px;border-top:2px solid #ddd"></div>
      </div>
      <div class="legacy-card" style="top:308px;height:290px">
        <svg class="abs" style="left:310px;top:14px" width="14" height="8"><path d="M1 7l6-6 6 6" stroke="#9bb" fill="none"/></svg>
        <div class="ofield" style="left:8px;top:36px;width:285px"><span class="leg">AddressLabelTag -e</span><svg class="abs" style="right:5px;top:15px" width="12" height="7"><path d="M0 0h12L6 7z" fill="#8fb4dd"/></svg></div>
        <div class="kebab" style="left:309px;top:50px;font-size:12px">•••</div>
        <div class="hint" style="left:21px;top:82px">Required</div>
        <div class="ofield" style="left:8px;top:100px;width:315px"><span class="leg">AddressLine1 -e</span>enter addressline1 -e</div>
        <div class="hint" style="left:21px;top:146px">Required</div>
        <div class="ofield" style="left:8px;top:164px;width:315px"><span class="leg">AddressLine2 -e</span>enter addressline2 -e</div>
        <div class="ofield" style="left:8px;top:228px;width:89px"><span class="leg">AddressCity</span>enter addr…</div>
        <div class="ofield" style="left:106px;top:228px;width:89px"><span class="leg">AddressState</span><svg class="abs" style="right:5px;top:15px" width="12" height="7"><path d="M0 0h12L6 7z" fill="#8fb4dd"/></svg></div>
        <div class="ofield" style="left:204px;top:228px;width:89px"><span class="leg">Zip -e</span>enter addr…</div>
      </div>
    </div>
    <div class="legacy-tabs">
      <div class="on"><svg width="12" height="12"><circle cx="6" cy="3.5" r="3" fill="#1B7ECC"/><path d="M0 12a6 5 0 0 1 12 0z" fill="#1B7ECC"/></svg>Contact</div>
      <div><svg width="12" height="12"><circle cx="6" cy="4" r="3.5" fill="#222"/><path d="M1 12a5 4 0 0 1 10 0z" fill="#222"/></svg>Quote</div>
      <div><svg width="13" height="12"><rect x="0" y="3" width="13" height="9" rx="1.5" fill="#222"/><rect x="4" y="0" width="5" height="4" rx="1" fill="none" stroke="#222" stroke-width="1.5"/></svg>WorkOrder</div>
      <div><svg width="12" height="12"><circle cx="6" cy="4" r="3.5" fill="#222"/><path d="M1 12a5 4 0 0 1 10 0z" fill="#222"/></svg>Invoice</div>
      <div><svg width="14" height="12"><g fill="#222"><circle cx="3" cy="6" r="1.4"/><circle cx="7" cy="6" r="1.4"/><circle cx="11" cy="6" r="1.4"/></g></svg>More</div>
    </div>
    <div class="home-bar" style="left:110px;width:123px;top:735px"></div>
  </div>

  <!-- refined add contact -->
  <div class="phone" style="left:475px;height:1260px">
    <div class="hero"></div>
    <div class="island"></div>
    <span class="time">9:41</span>
    <svg class="status-icons" width="56" height="12"><g fill="#fff"><rect x="0" y="8" width="3" height="4"/><rect x="4.5" y="6" width="3" height="6"/><rect x="9" y="3" width="3" height="9"/><rect x="13.5" y="0" width="3" height="12"/></g><path d="M21 4a9 9 0 0 1 13 0M24 7a5 5 0 0 1 7 0" stroke="#fff" stroke-width="1.8" fill="none"/><circle cx="27.5" cy="10" r="1.5" fill="#fff"/><rect x="36" y="1" width="20" height="10" rx="3" fill="#fff"/></svg>
    <svg class="abs" style="left:14px;top:60px" width="18" height="14"><path d="M17 7H2M7 1L1 7l6 6" stroke="#fff" stroke-width="1.8" fill="none"/></svg>
    <svg class="dots" width="20" height="4"><g fill="#fff"><circle cx="2" cy="2" r="2"/><circle cx="10" cy="2" r="2"/><circle cx="18" cy="2" r="2"/></g></svg>
    <div class="page-title">Add Contact</div>

    <div class="card" style="top:139px;height:400px">
      <div class="card-head">Contact Name<svg width="20" height="4"><g fill="#1B7ECC"><circle cx="2" cy="2" r="2"/><circle cx="10" cy="2" r="2"/><circle cx="18" cy="2" r="2"/></g></svg></div>
      <div class="field-label">Business Name</div><div class="input">Enter</div>
      <div class="field-label">First Name</div><div class="input">Enter</div>
      <div class="field-label">Middle Name</div><div class="input">Enter</div>
      <div class="field-label">Last Name</div><div class="input">Enter</div>
    </div>

    <div class="card" style="top:549px;height:562px">
      <div class="card-head">Contact Address<svg width="20" height="4"><g fill="#1B7ECC"><circle cx="2" cy="2" r="2"/><circle cx="10" cy="2" r="2"/><circle cx="18" cy="2" r="2"/></g></svg></div>
      <div class="field-label">Address Label Tag</div><div class="input">Select<svg width="12" height="18"><path d="M1 7l5 5 5-5" stroke="#1C1F34" stroke-width="1.5" fill="none"/></svg></div>
      <div class="field-label">Address Line 1</div><div class="input tall">Enter</div>
      <div class="field-label">Address Line 2</div><div class="input tall">Enter</div>
      <div class="field-label">City</div><div class="input">Enter</div>
      <div class="split">
        <div><div class="field-label">State</div><div class="input">Select<svg width="12" height="18"><path d="M1 7l5 5 5-5" stroke="#1C1F34" stroke-width="1.5" fill="none"/></svg></div></div>
        <div><div class="field-label">ZIP</div><div class="input">Enter</div></div>
      </div>
    </div>
    <div class="btn-save">Save</div>
    <div class="home-bar" style="left:112px;width:118px;top:1227px"></div>
  </div>

  <!-- legacy more -->
  <div class="legacy" style="left:935px">
    <div class="statusbar"><span class="time">3:01</span>
      <svg width="70" height="14"><g fill="#777"><circle cx="3" cy="11" r="1.2"/><circle cx="7" cy="11" r="1.2"/><circle cx="11" cy="11" r="1.2"/><circle cx="15" cy="11" r="1.2"/></g><path d="M24 5a10 10 0 0 1 14 0M27 8a6 6 0 0 1 8 0" stroke="#fff" stroke-width="2" fill="none"/><circle cx="31" cy="11" r="1.6" fill="#fff"/><rect x="45" y="2" width="21" height="10" rx="3" fill="#fff"/></svg>
    </div>
    <div class="legacy-head" style="box-shadow:0 3px 4px rgba(0,0,0,.15)">
      <div class="sub" style="top:16px;font-size:15px">More</div>
      <div class="kebab" style="left:312px;top:12px">•••</div>
    </div>
    <div class="menu-row"><svg width="14" height="12"><path d="M0 11h14M1 3l11 4 2-3-9-3z" fill="#111" stroke="#111"/></svg>Flight</div>
    <div class="menu-row"><svg width="14" height="12"><circle cx="4" cy="2.5" r="2" fill="#111"/><circle cx="10" cy="2.5" r="2" fill="#111"/><rect x="2" y="5" width="4" height="7" fill="#111"/><rect x="8" y="5" width="4" height="7" fill="#111"/></svg>Login</div>
    <div class="menu-row"><svg width="14" height="12"><circle cx="7" cy="3.5" r="3" fill="#111"/><path d="M1 12a6 5 0 0 1 12 0z" fill="#111"/></svg>Account</div>
    <div class="menu-row"><svg width="14" height="12"><path d="M2 0h10v8l-4 4H2z" fill="#111"/></svg>Calendar</div>
    <div class="menu-row"><svg width="14" height="12"><circle cx="7" cy="3" r="2.5" fill="#111"/><circle cx="2.5" cy="4" r="2" fill="#111"/><circle cx="11.5" cy="4" r="2" fill="#111"/><path d="M2 12a5 5 0 0 1 10 0z" fill="#111"/></svg>Users</div>
    <div class="menu-row"><svg width="14" height="12"><path d="M7 0l7 6h-2v6H9V8H5v4H2V6H0z" fill="#111"/></svg>Dashboard</div>
    <div class="menu-row"><svg width="14" height="12"><path d="M0 2l4-1v10l-4 1zM5 1l4 1v10l-4-1zM10 2l4-1v10l-4 1z" fill="#111"/></svg>Tracking</div>
    <div class="menu-row"><svg width="14" height="12"><rect x="0" y="3" width="14" height="3" fill="#111"/><rect x="1" y="7" width="12" height="5" fill="#111"/></svg>Outreach Event</div>
    <div class="menu-row"><svg width="14" height="12"><path d="M1 11l9-9 2 2-9 9z" fill="#111"/></svg>Maintenance Resource</div>
    <div class="menu-row"><svg width="14" height="12"><circle cx="7" cy="6" r="4.5" fill="none" stroke="#111" stroke-width="3" stroke-dasharray="2 1.5"/><circle cx="7" cy="6" r="2.5" fill="#111"/></svg>Setting</div>
    <div class="legacy-tabs">
      <div><svg width="12" height="12"><circle cx="6" cy="3.5" r="3" fill="#222"/><path d="M0 12a6 5 0 0 1 12 0z" fill="#222"/></svg>Contact</div>
      <div><svg width="12" height="12"><circle cx="6" cy="4" r="3.5" fill="#222"/><path d="M1 12a5 4 0 0 1 10 0z" fill="#222"/></svg>Pilot</div>
      <div><svg width="14" height="12"><path d="M0 6h14M7 0l2 6-2 6M2 3l1 3-1 3" stroke="#222" stroke-width="2.2" fill="none"/></svg>Plane</div>
      <div><svg width="12" height="12"><path d="M4 0h2v6l5 1v5H3L1 8l3-1z" fill="#222"/></svg>Flt Request</div>
      <div class="on"><svg width="14" height="12"><g fill="#1B7ECC"><circle cx="3" cy="6" r="1.4"/><circle cx="7" cy="6" r="1.4"/><circle cx="11" cy="6" r="1.4"/></g></svg>More</div>
    </div>
    <div class="home-bar" style="left:110px;width:123px;top:735px"></div>
  </div>

  <!-- refined more -->
  <div class="phone" style="left:1304px;height:766px">
    <div class="hero"></div>
    <div class="island"></div>
    <span class="time">9:41</span>
    <svg class="status-icons" width="56" height="12"><g fill="#fff"><rect x="0" y="8" width="3" height="4"/><rect x="4.5" y="6" width="3" height="6"/><rect x="9" y="3" width="3" height="9"/><rect x="13.5" y="0" width="3" height="12"/></g><path d="M21 4a9 9 0 0 1 13 0M24 7a5 5 0 0 1 7 0" stroke="#fff" stroke-width="1.8" fill="none"/><circle cx="27.5" cy="10" r="1.5" fill="#fff"/><rect x="36" y="1" width="20" height="10" rx="3" fill="#fff"/></svg>
    <svg class="dots" width="20" height="4"><g fill="#fff"><circle cx="2" cy="2" r="2"/><circle cx="10" cy="2" r="2"/><circle cx="18" cy="2" r="2"/></g></svg>
    <div class="page-title">More</div>
    <div class="tiles">
      <div class="tile"><span class="ico" style="background:var(--cyan)"><svg width="18" height="16"><path d="M1 14h16M2 5l12 4 2-3-10-4z" stroke="#fff" stroke-width="1.4" fill="none"/></svg></span>Flight</div>
      <div class="tile"><span class="ico" style="background:var(--green)"><svg width="18" height="18"><path d="M8 2h8v14H8M1 9h10M8 6l3 3-3 3" stroke="#fff" stroke-width="1.5" fill="none"/></svg></span>Login</div>
      <div class="tile"><span class="ico" style="background:var(--orange)"><svg width="18" height="18"><circle cx="9" cy="9" r="8" stroke="#fff" stroke-width="1.4" fill="none"/><circle cx="9" cy="7" r="3" stroke="#fff" stroke-width="1.4" fill="none"/><path d="M4 15a6 5 0 0 1 10 0" stroke="#fff" stroke-width="1.4" fill="none"/></svg></span>Account</div>
      <div class="tile"><span class="ico" style="background:var(--yellow)"><svg width="18" height="18"><rect x="1.5" y="3" width="15" height="13" rx="2" stroke="#fff" stroke-width="1.4" fill="none"/><path d="M1.5 7h15M5 1v4M13 1v4" stroke="#fff" stroke-width="1.4"/></svg></span>Calendar</div>
      <div class="tile"><span class="ico" style="background:var(--pink)"><svg width="18" height="18"><circle cx="6" cy="6" r="3" stroke="#fff" stroke-width="1.4" fill="none"/><circle cx="12.5" cy="6" r="2.5" stroke="#fff" stroke-width="1.4" fill="none"/><path d="M1 16a5 5 0 0 1 10 0M11 11a5 5 0 0 1 6 5" stroke="#fff" stroke-width="1.4" fill="none"/></svg></span>Users</div>
      <div class="tile"><span class="ico" style="background:var(--violet)"><svg width="18" height="18"><path d="M2 8l7-6 7 6v8H2zM7 16v-5h4v5" stroke="#fff" stroke-width="1.4" fill="none"/></svg></span>Dashboard</div>
      <div class="tile"><span class="ico" style="background:var(--cyan)"><svg width="18" height="18"><path d="M1 4l5-2 6 2 5-2v12l-5 2-6-2-5 2zM6 2v12M12 4v12" stroke="#fff" stroke-width="1.4" fill="none"/></svg></span>Tracking</div>
      <div class="tile"><span class="ico" style="background:var(--green)"><svg width="18" height="18"><rect x="1.5" y="5" width="15" height="4" stroke="#fff" stroke-width="1.4" fill="none"/><path d="M3 9v7h12V9M9 5v11M9 5C6 1 3 3 6 5M9 5c3-4 6-2 3 0" stroke="#fff" stroke-width="1.4" fill="none"/></svg></span>Outreach<br>Event</div>
      <div class="tile"><span class="ico" style="background:var(--orange)"><svg width="18" height="18"><path d="M2 16l8-8M10 8a4 4 0 1 0 0-5l3 3-2 2-3-3" stroke="#fff" stroke-width="1.5" fill="none"/></svg></span>Maintenance<br>Resource</div>
      <div class="tile"><span class="ico" style="background:var(--yellow)"><svg width="18" height="18"><circle cx="9" cy="9" r="6.5" stroke="#fff" stroke-width="2.5" fill="none" stroke-dasharray="3 2"/><circle cx="9" cy="9" r="2.5" stroke="#fff" stroke-width="1.4" fill="none"/></svg></span>Setting</div>
    </div>
    <div class="tabbar">
      <div><svg width="18" height="20"><rect x="2" y="1" width="14" height="18" rx="2" stroke="#7C848B" stroke-width="1.4" fill="none"/><circle cx="9" cy="8" r="2.5" stroke="#7C848B" stroke-width="1.4" fill="none"/><path d="M5 15a4 3 0 0 1 8 0" stroke="#7C848B" stroke-width="1.4" fill="none"/></svg>Contact</div>
      <div><svg width="18" height="20"><circle cx="9" cy="7" r="4" stroke="#7C848B" stroke-width="1.4" fill="none"/><path d="M4 3h10M2 19a7 6 0 0 1 14 0" stroke="#7C848B" stroke-width="1.4" fill="none"/></svg>Pilot</div>
      <div><svg width="18" height="20"><path d="M9 1v18M1 11l8-3 8 3M5 19l4-2 4 2" stroke="#7C848B" stroke-width="1.4" fill="none"/></svg>Plane</div>
      <div><svg width="18" height="20"><path d="M7 11V3a1.5 1.5 0 0 1 3 0v6l5 1v5l-2 4H7l-3-5 2-2z" stroke="#7C848B" stroke-width="1.4" fill="none"/></svg>Flt Request</div>
      <div class="on"><svg width="18" height="20"><path d="M2 5h14M2 10h14M2 15h14" stroke="#1B7ECC" stroke-width="1.6"/></svg>More</div>
    </div>
    <div class="home-bar" style="left:112px;width:118px;top:733px"></div>
  </div>
</div>
</body>
</html>
```